Blood Testing Health App

We are looking for a graphics designer to create a web app for us so that we may insert it into a health management website system.
For branding purposes we are at www.Vantiqor.com and we are revamping our website... Example of new colors attached.
How we work...
We are a blood testing company based in the USA.
We offer a blood testing service nationwide in the USA.
We allow customers to order tests directly from us, visit a lab, have their blood drawn, or submit a urine sample, the lab tests it and they send the results back to our computer system and we share it with the customer.
The benefits of this are the customer does not need to go to the doctor and pay for the doctors visit to order these tests, which save them money. The tests are cheaper than going through the doctor. The customer simply uses us to get the test and the results and they can then take the results to their doctor... this process has saved them money. Others may be interested in regular check ups for blood work etc... and this allows them to do it with out needing a doctor, or if you have no insurance, this is a cheaper option too. We are quicker than a doctor, customers do not need appointments etc.
Hopefully you now have a better understanding as to what we do.
Here is the spec.
The app screen size is 750 px wide by 700 px high. ( A pdf is attached to show where the app is going to go, it is on page 3 of the pdf) The customer will have the ability to scroll… therefore the length of the page can be longer.
The app will consist of the following sections
Entry Page –
This will be the first page the user sees upon opening the app. This will be where they are directed from to the sections of the app discussed below. This needs to be branded for VantiQor with a modern look.
1 – Order Test (Giving them the ability to purchase a blood test within the app)
2 – VantiQor Dashboard (A dashboard that has everything they could need to use our service_
How it works Section on entry page – this will be a simple set of graphics showing how the service works. We already have the graphics for this, they do not need to be built again. They are attached to this brief
Basic structure of sections –
Order Test –
This page contains all tests, filed in categories – and Sub categories – Each test needs a link to an Information section – Price – Buy Now – Cart Process
VantiQor Dashboard –
A page of icons along the top of the app
- My Confirmation
- My Nearest Lab
- My Receipt
- My Orders
- My Account
- My Results
- My Inbox
- Contact Us
Sections in more detail -
Order A Test –
Show all categories/ sub categories – There are 23 categories, 14 sub categories, and within these categories are 300 tests - Here is the information for the categories etc - http://www.vantiqor.com/panels.aspx?PanelGroupID=4 Just in case it helps :)
We need to present this in a graphic format that is spacious, modern (brimlake, kivvo web appearance is the direction we are going for) We need it to be clear and not overwhelming to the customer.
Functionality idea…
Customer clicks category/ subcategory and tests appear.
Customer sees small 35 word description. For more information the test opens into a lightbox or expand the container which ever graphic designer believes to be most visually appealing
Buy Now must always be visible, along with price of the test
Buying process explained – Customer clicks buy now –
They are then taken to a Review Order screen ( This contains Order summary and choose payment method – insert payment details )
– Confirm payment –
Confirmation screen appears, thanking them.
They are then taken to the VantiQor Dashboard...
VantiQor Dashboard –
"My Confirmation" - Print Confirmation Order (PDF is in brief, we want this web based not a pdf download)
"My Nearest Lab Location" - This does not need to be designed because the web developer has this part under control, but we do need the icon in the dashboard
"My Receipt" - Print receipt - This does not exist in our system yet. So we need to create this from scratch - It will need to have - The test they are purchasing and the amount of the test - The customers name - The order ID - Must provide printer friendly option too
"My Orders" - This will have a list of orders - At the end of each order will be a status update of either "Test results" "Open order"
A graphic table format would be perfect. This will be linked to relevant results if they have been received. I have also attached a version of what the customer currently sees on our website. We know it is nasty ;) We are redesigning... but the information is there for this section to help design it with the right info. If the results are ready it will say in this list.
"Results Ready" will be a link to show those results once the customer has clicked the link, and the results will appear in the app, under the icons. There must be a printer friendly version too.
"My Results" Developer will sort this page out but we need the icon... It will be exactly like my orders but only show test results
"My Account" - This will be a place for them to update their personal information - Name, DOB, Address, Email Address
"My Inbox" - An inbox interface - Our way of contacting the customer for promotions we are running etc – We need a design of how this screen will appear. We also need the icon in the dashboard to have a notification on it if there are messages in the customers inbox. A little red 1, or circle with number of messages in the inbox.
"Customer Service" - This does not need to be designed because the web developer has this part under control, but we do need the icon in the dashboard
Icons appear along the top of app ( example - Mac icons/ iphone app icons) When the customer clicks an icon the content always appears below the icons
Here is more information for the icons and what should appear when each icon is clicked.
Screens to be designed –
Entry Page
Order A Test Page
Review Order Screen/Payment Screen - Show a lightbox that shows payment has been confirmed. Customer clicks close and are on the Confirmation Screen
VantiQor Dashboard - Screens mentioned in detail above
We can't wait to see your designs!
Please email any questions.
Hi all this is the first time we have used pixel harbor and understand the budget was too low for this project. We have now increased the budget to $2,000 and extended the deadline by another week
Hi all we are receiving some really great designs. I just added an example of the space that the web app will be going into... It is called "morvelapp.pdf"
Hi guys updated the brief. Hopefully this will help with the dashboard part of the design

```html
<!DOCTYPE html>
<html lang="en">
<head>
<meta charset="utf-8">
<title>VantiQor – Allergy Tests</title>
<link rel="stylesheet" href="https://fonts.googleapis.com/css2?family=Open+Sans:wght@400;600;700&family=Arimo:wght@700&display=swap">
<style>
:root{
  --green:#7dc034;
  --orange:#f04e00;
  --orange-light:#ff7a2e;
  --blue:#1f6fb8;
  --ink:#222;
  --text:#333;
  --bar:#e3e3e3;
  --panel:#e9e9e9;
  --thead:#535853;
  --line:#e2e2e2;
  --white:#fff;
}
*{box-sizing:border-box;margin:0;padding:0}
html,body{width:725px;height:1200px;overflow:hidden;background:var(--white)}
body{font-family:"Open Sans",sans-serif;color:var(--text)}
.app{width:750px;height:1241px;transform:scale(.96667);transform-origin:0 0;position:relative}

/* header */
.site-header{height:100px;position:relative;background:var(--white)}
.brand-name{position:absolute;left:18px;top:44px;font-size:38px;font-weight:400;color:#333;letter-spacing:-.5px;line-height:1}
.main-nav{position:absolute;left:340px;top:30px;display:flex;gap:2px}
.nav-tab{width:124px;height:70px;display:flex;flex-direction:column;align-items:center;justify-content:flex-end;padding-bottom:16px;font-size:11px;text-transform:uppercase;color:#999;border-radius:8px 8px 0 0}
.nav-tab svg{margin-bottom:8px}
.nav-tab.is-active{background:var(--bar);color:var(--green)}
.social{position:absolute;right:17px;top:63px;display:flex;gap:10px}
.social span{width:29px;height:29px;border-radius:50%;background:var(--green)}

/* filters */
.filter-bar{height:68px;background:linear-gradient(#e3e3e3,#dcdcdc);position:relative}
.select{position:absolute;top:19px;height:31px;background:var(--white);border-radius:3px;font-size:13px;color:#333;padding:7px 13px;box-shadow:0 1px 2px rgba(0,0,0,.12)}
.select svg{position:absolute;right:10px;top:9px}
.select--category{left:18px;width:200px}
.select--test{left:226px;width:200px}
.search{position:absolute;left:493px;top:19px;width:240px;height:31px;background:var(--white);border-radius:3px;font-size:13px;padding:7px 16px;box-shadow:0 1px 2px rgba(0,0,0,.12)}
.search-btn{position:absolute;right:5px;top:5px;width:32px;height:21px;background:#4a4a4a;border-radius:3px;display:flex;align-items:center;justify-content:center}

/* category intro */
.category-intro{height:165px;background:linear-gradient(#f2f2f2,#dedede);position:relative}
.category-icon{position:absolute;left:33px;top:26px;width:92px;height:92px;border-radius:50%;background:radial-gradient(circle at 40% 35%,#ffffff,#d5d5d5 70%,#bcbcbc);box-shadow:0 2px 4px rgba(0,0,0,.25);border:3px solid #fafafa}
.category-copy{position:absolute;left:172px;top:24px;width:545px}
.category-title{font-size:22px;font-weight:700;color:var(--orange);line-height:1.2}
.category-question{font-size:17px;font-weight:700;color:var(--ink);margin-top:4px}
.category-desc{font-size:13px;line-height:1.35;color:#222;margin-top:2px}

/* tests panel */
.tests-panel{position:absolute;left:23px;top:350px;width:712px;height:858px;background:var(--panel);border-radius:8px;padding:15px 11px}
.tests-card{background:var(--white);border-radius:6px;overflow:hidden;height:830px}
.tests-heading{height:47px;background:var(--green);color:var(--white);font-size:19px;font-weight:400;padding:10px 15px;border-radius:6px 6px 0 0}
.tests-head-row{height:37px;background:var(--thead);color:var(--white);font-size:13px;position:relative}
.tests-head-row span{position:absolute;top:10px}
.col-name{left:25px}.col-price{left:562px}

.test-row{position:relative;border-bottom:1px solid var(--line);background:linear-gradient(#fff 60%,#f6f6f6)}
.test-row--compact{height:113px;padding:14px 23px}
.test-name{font-size:17px;font-weight:700;color:var(--blue)}
.test-summary{font-size:13px;line-height:1.35;color:#222;width:470px;margin-top:2px}
.more-link{font-size:11px;font-weight:700;color:var(--blue);margin-top:6px;display:flex;align-items:center;gap:6px}
.row-price{position:absolute;left:561px;top:16px;font-size:22px;color:var(--orange)}
.btn-small{position:absolute;left:560px;top:52px;width:99px;height:23px;border-radius:4px;background:linear-gradient(var(--orange-light),var(--orange));border:1px solid #d84400;color:var(--white);font-family:"Arimo",sans-serif;font-size:9px;font-weight:700;display:flex;align-items:center;justify-content:center;gap:7px;letter-spacing:-.2px}

.test-row--open{height:397px;padding:14px 23px;background:linear-gradient(#fff 70%,#f3f3f3)}
.test-detail{font-size:13px;line-height:1.3;color:#222;margin-top:14px;width:648px}
.included-label{font-size:13px;font-weight:700;color:#222;margin-top:21px;text-transform:uppercase}
.included-list{list-style:none;margin-top:10px;padding-left:20px}
.included-list li{display:flex;align-items:center;gap:10px;font-size:15px;color:var(--blue);margin-bottom:8px}
.detail-price{font-size:19px;font-weight:600;color:#222;margin:32px 0 0 18px}
.detail-price b{color:var(--orange);font-weight:700}
.btn-large{margin:9px 0 0 16px;width:178px;height:40px;border-radius:8px;background:linear-gradient(var(--orange-light),var(--orange));border:1px solid #d84400;color:var(--white);font-family:"Arimo",sans-serif;font-size:16px;font-weight:700;display:flex;align-items:center;justify-content:center;gap:12px;box-shadow:0 1px 3px rgba(0,0,0,.2)}
</style>
</head>
<body>
<div class="app">
  <header class="site-header">
    <span class="brand-name">VantiQor</span>
    <nav class="main-nav">
      <div class="nav-tab is-active">
        <svg width="34" height="24" viewBox="0 0 34 24"><rect x="5" y="2" width="24" height="16" rx="2" fill="#7dc034"/><rect x="8" y="5" width="18" height="10" fill="#e3e3e3"/><rect x="1" y="19" width="32" height="3" rx="1.5" fill="#7dc034"/></svg>
        Order a Test
      </div>
      <div class="nav-tab">
        <svg width="28" height="28" viewBox="0 0 28 28"><rect x="8" y="2" width="18" height="16" fill="none" stroke="#999" stroke-width="2"/><rect x="3" y="9" width="18" height="16" fill="#fff" stroke="#999" stroke-width="2"/><rect x="3" y="9" width="18" height="4" fill="#999"/></svg>
        Dashboard
      </div>
    </nav>
    <div class="social"><span></span><span></span><span></span></div>
  </header>

  <section class="filter-bar">
    <div class="select select--category">Allergies
      <svg width="16" height="14" viewBox="0 0 16 14"><path d="M0 0h16L8 14z" fill="#333"/></svg></div>
    <div class="select select--test">Choose A Test
      <svg width="16" height="14" viewBox="0 0 16 14"><path d="M0 0h16L8 14z" fill="#333"/></svg></div>
    <div class="search">Search for a test
      <span class="search-btn"><svg width="18" height="14" viewBox="0 0 18 14"><circle cx="6" cy="6" r="4.3" fill="none" stroke="#fff" stroke-width="2"/><path d="M9.5 9l6 4" stroke="#fff" stroke-width="2.5" stroke-linecap="round"/></svg></span>
    </div>
  </section>

  <section class="category-intro">
    <div class="category-icon" role="img" aria-label="Allergy category icon: gloved hand with skin rash"></div>
    <div class="category-copy">
      <h1 class="category-title">Allergies</h1>
      <h2 class="category-question">What are You Allergic To?</h2>
      <p class="category-desc">Could be pollen, animal dander, insect bites, food or something else entirely! What we think we're allergic to is not always what's causing an allergic reaction</p>
    </div>
  </section>

  <section class="tests-panel">
    <div class="tests-card">
      <h3 class="tests-heading">Choose An Allergy Test</h3>
      <div class="tests-head-row"><span class="col-name">Test Name</span><span class="col-price">Price</span></div>

      <article class="test-row test-row--compact">
        <h4 class="test-name">Comprehensive Food Allergy Profile</h4>
        <p class="test-summary">Let one blood test screen over 96 foods including fruits, vegetables, nuts, grains, dairy and animal products to help you manage your dietary needs.</p>
        <div class="more-link">more details <svg width="5" height="6" viewBox="0 0 5 6"><path d="M0 0l5 3-5 3z" fill="#1f6fb8"/></svg></div>
        <div class="row-price">$93.00</div>
        <div class="btn-small">ADD TO CART <svg width="12" height="12" viewBox="0 0 12 12"><circle cx="6" cy="6" r="5.5" fill="#8a2a00"/><path d="M3 6h5M6 3.5L8.5 6 6 8.5" stroke="#fff" stroke-width="1.4" fill="none"/></svg></div>
      </article>

      <article class="test-row test-row--open">
        <h4 class="test-name">Expanded Food Allergy Test</h4>
        <p class="test-detail">This Profile includes testing for the following 48 foods: Almond , Carrot, Crab, Lemon, White Potato, Tea, Apple, Cheese, Egg, Mushroom, Rice, Tomato, Banana ,Chicken, Garlic, Oat ,Rye, Tuna, Beef, Chili Pepper, Grape, Onion, Safflower, Turkey, Black Pepper, Chocolate, Green Bean, Orange, Shrimp , Vanilla, Broccoli, Coffee, Haddock, Oyster, Soybean, Wheat, Cabbage, Corn, Halibut, Peanut, Strawberry, Baker's Yeast, Cantaloupe, Cow's Milk, Lamb, Pork, Sugar Cane, Brewer's Yeast. IGE</p>
        <p class="included-label">Tests Included</p>
        <ul class="included-list">
          <li><svg width="18" height="18" viewBox="0 0 18 18"><circle cx="9" cy="9" r="9" fill="#1f6fb8"/><path d="M5 9.2l2.8 2.8L13 6.5" stroke="#fff" stroke-width="2" fill="none"/></svg>Allergen Profile Food</li>
          <li><svg width="18" height="18" viewBox="0 0 18 18"><circle cx="9" cy="9" r="9" fill="#1f6fb8"/><path d="M5 9.2l2.8 2.8L13 6.5" stroke="#fff" stroke-width="2" fill="none"/></svg>Expanded Food Allergy Test</li>
        </ul>
        <p class="detail-price">Test Price: <b>$295.00</b></p>
        <div class="btn-large">ADD TO CART <svg width="20" height="20" viewBox="0 0 20 20"><circle cx="10" cy="10" r="9.5" fill="#8a2a00"/><path d="M5 10h8M10 6l4 4-4 4" stroke="#fff" stroke-width="2" fill="none"/></svg></div>
      </article>

      <article class="test-row test-row--compact">
        <h4 class="test-name">Comprehensive Food Allergy Profile</h4>
        <p class="test-summary">Let one blood test screen over 96 foods including fruits, vegetables, nuts, grains, dairy and animal products to help you manage your dietary needs.</p>
        <div class="more-link">more details <svg width="5" height="6" viewBox="0 0 5 6"><path d="M0 0l5 3-5 3z" fill="#1f6fb8"/></svg></div>
        <div class="row-price">$93.00</div>
        <div class="btn-small">ADD TO CART <svg width="12" height="12" viewBox="0 0 12 12"><circle cx="6" cy="6" r="5.5" fill="#8a2a00"/><path d="M3 6h5M6 3.5L8.5 6 6 8.5" stroke="#fff" stroke-width="1.4" fill="none"/></svg></div>
      </article>

      <article class="test-row test-row--compact">
        <h4 class="test-name">Comprehensive Food Allergy Profile</h4>
        <p class="test-summary">Let one blood test screen over 96 foods including fruits, vegetables, nuts, grains, dairy and animal products to help you manage your dietary needs.</p>
        <div class="more-link">more details <svg width="5" height="6" viewBox="0 0 5 6"><path d="M0 0l5 3-5 3z" fill="#1f6fb8"/></svg></div>
        <div class="row-price">$93.00</div>
        <div class="btn-small">ADD TO CART <svg width="12" height="12" viewBox="0 0 12 12"><circle cx="6" cy="6" r="5.5" fill="#8a2a00"/><path d="M3 6h5M6 3.5L8.5 6 6 8.5" stroke="#fff" stroke-width="1.4" fill="none"/></svg></div>
      </article>
    </div>
  </section>
</div>
</body>
</html>
```